RB Halden Electric Yard Sign

Looking to have a yard sign designed that we can place at projects we are working on. Most likely will be 18" H x 24" W but flexible that we can increase the size if necessary. It should include our logo, our phone # 201-555-0147, website rbhaldenelectric.example and slogan, Safe wiring, honest work, lasting results. Colors should match our brand.

```html
<!DOCTYPE html>
<html lang="en">
<head>
<meta charset="utf-8">
<title>RB Halden Electric Yard Sign</title>
<link href="https://fonts.googleapis.com/css2?family=Krona+One&family=Russo+One&family=Saira+Condensed:ital,wght@1,600&display=swap" rel="stylesheet">
<style>
  :root {
    --navy: #0f3358;
    --red: #e0202e;
    --white: #ffffff;
    --backdrop: #4a4a4a;
  }
  html, body {
    margin: 0;
    width: 1200px;
    height: 1001px;
    overflow: hidden;
    background: var(--backdrop);
  }
  .yard-sign {
    position: absolute;
    left: 50px;
    top: 88px;
    width: 1100px;
    height: 825px;
    background: var(--white);
  }
  .brand-name {
    position: absolute;
    left: 0;
    right: 0;
    top: 205px;
    margin: 0;
    text-align: center;
    font-family: "Russo One", sans-serif;
    font-weight: 400;
    font-size: 88px;
    line-height: 1;
    letter-spacing: 2px;
    color: var(--red);
    text-transform: uppercase;
    white-space: nowrap;
  }
  .rule {
    position: absolute;
    left: 0;
  }
  .contact-band {
    position: absolute;
    left: 0;
    top: 394px;
    width: 1100px;
    height: 256px;
    background: var(--navy);
    border-top: 10px solid var(--red);
    border-bottom: 10px solid var(--red);
    box-sizing: border-box;
  }
  .contact-band::before,
  .contact-band::after {
    content: "";
    position: absolute;
    left: 0;
    right: 0;
    height: 6px;
    background: var(--white);
  }
  .contact-band::before { top: 0; }
  .contact-band::after { bottom: 0; }
  .contact-line {
    position: absolute;
    left: 0;
    right: 0;
    display: flex;
    align-items: center;
    justify-content: center;
    gap: 14px;
    color: var(--white);
    font-family: "Krona One", sans-serif;
    white-space: nowrap;
  }
  .phone { top: 40px; font-size: 74px; line-height: 1; }
  .website { top: 162px; font-size: 36px; line-height: 1; }
  .slogan {
    position: absolute;
    left: 0;
    right: 0;
    top: 690px;
    margin: 0;
    text-align: center;
    font-family: "Saira Condensed", sans-serif;
    font-style: italic;
    font-weight: 600;
    font-size: 60px;
    line-height: 1;
    color: var(--navy);
    text-transform: uppercase;
    white-space: nowrap;
  }
</style>
</head>
<body>
  <div class="yard-sign">
    <h1 class="brand-name">RB Halden Electric</h1>

    <svg class="rule" style="top:318px" width="1100" height="20" viewBox="0 0 1100 20" aria-hidden="true">
      <polygon points="130,6 970,6 955,10 145,10" fill="var(--red)"/>
      <polygon points="145,11 955,11 945,15 155,15" fill="var(--navy)"/>
    </svg>

    <div class="contact-band">
      <div class="contact-line phone">
        <svg width="44" height="56" viewBox="0 0 24 30" aria-hidden="true">
          <path d="M6 2c2 0 3 1 3.5 3l1 4c.3 1.3-.4 2-1.5 2.6-.8.4-1 1-.7 2 1.2 3.6 2.6 6.2 4.8 8.6.6.6 1.3.7 2 .1 1-.8 2-1.2 3.1-.4l3 2.4c1.300 1 1.2 2.4.2 3.6C18 30 15 30 12 27 6.5 21.5 3 14 3 7.5 3 4.5 4 2 6 2z" fill="var(--red)"/>
        </svg>
        <span>201-555-0147</span>
      </div>
      <div class="contact-line website">
        <svg width="36" height="36" viewBox="0 0 24 24" aria-hidden="true" fill="none" stroke="var(--red)" stroke-width="1.8">
          <circle cx="12" cy="12" r="10"/>
          <ellipse cx="12" cy="12" rx="4.5" ry="10"/>
          <line x1="2" y1="12" x2="22" y2="12"/>
          <line x1="4" y1="6.5" x2="20" y2="6.5"/>
          <line x1="4" y1="17.5" x2="20" y2="17.5"/>
        </svg>
        <span>rbhaldenelectric.example</span>
      </div>
    </div>

    <p class="slogan">Safe wiring, honest work, lasting results</p>

    <svg class="rule" style="top:772px" width="1100" height="24" viewBox="0 0 1100 24" aria-hidden="true">
      <polygon points="15,6 1085,6 1065,11 35,11" fill="var(--red)"/>
      <polygon points="35,12 1065,12 1050,18 50,18" fill="var(--navy)"/>
    </svg>
  </div>
</body>
</html>
```